Stylish Business Cards Wanted

- DOUBLE SIDED Design Required -

High end, edgy cards for a corporate and personal stylist. Must include logo,
Name: Belinda Harwick
Title: Director and Stylist
telephone : +61 8 7142 5809
email: belinda@theloombriefing.example
website: theloombriefing.example
Tag: Corporate Workwear & Uniform Specialist | Personal Stylist
Would like nice icons for telephone, email, website

Target Market(s)

Businesses wanting stylish uniforms, people wanting stylish wardrobes

Industry/Entity Type

Corporate Workwear Stylist

Contact Information for Business Card

I would like black, white and gold foiling incorporated in the design - possibly a touch of the other colours on my branding guide attached Name: Belinda Harwick Title: Director and Stylist telephone : +61 8 7142 5809 email: belinda@theloombriefing.example website: theloombriefing.example Tag: Corporate Workwear & Uniform Specialist | Personal Stylist Would like nice icons for telephone, email, website

Font styles to use
Other font styles liked:
• Raleway

Colors

Designer to choose colors to be used in the design.

Requirements
Must have
• Gold foil accents

```html
<!DOCTYPE html>
<html lang="en">
<head>
<meta charset="utf-8">
<title>The Loom Briefing — Business Cards</title>
<link rel="stylesheet" href="https://fonts.googleapis.com/css2?family=Dancing+Script:wght@600;700&family=Raleway:wght@400;500;600&family=Roboto:wght@400&display=swap">
<style>
  :root {
    --backdrop: #c8c8c8;
    --navy: #141b2e;
    --gold: #d9ad45;
    --white: #f4f4f4;
    --soft-white: #e6e6e6;
  }
  * { box-sizing: border-box; margin: 0; padding: 0; }
  html, body {
    width: 1200px;
    height: 852px;
    overflow: hidden;
    background: var(--backdrop);
  }
  .stage {
    position: relative;
    width: 1200px;
    height: 852px;
  }
  .card {
    position: absolute;
    width: 520px;
    height: 300px;
    background: var(--navy);
    border-radius: 22px;
    box-shadow: 0 6px 16px rgba(0, 0, 0, 0.25);
    overflow: hidden;
  }
  .card--front { left: 110px; top: 110px; }
  .card--back { left: 570px; top: 440px; }

  .brand {
    font-family: "Raleway", sans-serif;
    font-weight: 600;
    text-transform: uppercase;
    letter-spacing: 0.14em;
    line-height: 1.15;
    text-align: center;
  }
  .card--front .brand {
    position: absolute;
    left: 0; right: 0; top: 50%;
    transform: translateY(-50%);
    color: var(--gold);
    font-size: 34px;
  }
  .card--back .brand {
    position: absolute;
    right: 40px; top: 46px;
    color: var(--white);
    font-size: 20px;
    text-align: right;
  }

  .holder {
    position: absolute;
    left: 40px; top: 108px;
  }
  .holder__name {
    font-family: "Dancing Script", cursive;
    font-weight: 700;
    font-size: 30px;
    color: var(--gold);
    line-height: 1;
  }
  .holder__title {
    font-family: "Roboto", sans-serif;
    font-size: 12px;
    color: var(--soft-white);
    margin-top: 6px;
  }

  .contacts {
    position: absolute;
    left: 40px; top: 178px;
    list-style: none;
  }
  .contacts li {
    display: flex;
    align-items: center;
    gap: 10px;
    font-family: "Roboto", sans-serif;
    font-size: 13px;
    color: var(--white);
    height: 20px;
  }
  .contacts svg {
    width: 12px; height: 12px;
    fill: none;
    stroke: var(--gold);
    stroke-width: 1.6;
    stroke-linecap: round;
    stroke-linejoin: round;
  }

  .tagline {
    position: absolute;
    left: 40px; bottom: 26px;
    font-family: "Dancing Script", cursive;
    font-weight: 600;
    font-size: 16px;
    color: var(--white);
  }
  .tagline__divider {
    color: var(--gold);
    margin: 0 6px;
  }
</style>
</head>
<body>
<main class="stage">
  <section class="card card--front" aria-label="Card front">
    <p class="brand">The Loom<br>Briefing</p>
  </section>

  <section class="card card--back" aria-label="Card back">
    <p class="brand">The Loom<br>Briefing</p>

    <div class="holder">
      <h1 class="holder__name">Belinda Harwick</h1>
      <p class="holder__title">Director and Stylist</p>
    </div>

    <ul class="contacts">
      <li>
        <svg viewBox="0 0 12 12" aria-hidden="true"><circle cx="6" cy="6" r="5.2"/><path d="M4.2 3.4 5 4.8 4.5 5.4c.4.9 1.1 1.6 2 2l.6-.5 1.4.8-.5 1c-2.3-.3-4.3-2.3-4.6-4.6z"/></svg>
        +61 8 7142 5809
      </li>
      <li>
        <svg viewBox="0 0 12 12" aria-hidden="true"><rect x="1" y="2.5" width="10" height="7" rx="0.6"/><path d="M1 3l5 3.8L11 3"/></svg>
        belinda@theloombriefing.example
      </li>
      <li>
        <svg viewBox="0 0 12 12" aria-hidden="true"><circle cx="6" cy="6" r="5"/><path d="M1 6h10M6 1c-2.4 2.8-2.4 7.2 0 10M6 1c2.4 2.8 2.4 7.2 0 10"/></svg>
        www.theloombriefing.example
      </li>
    </ul>

    <p class="tagline">Corporate Workwear &amp; Uniform Specialist<span class="tagline__divider">|</span>Personal Stylist</p>
  </section>
</main>
</body>
</html>
```